Animal Eye Clinic needs a Business card

We are a new veterinary ophthalmology practice (Ridgeline Pet Vision Care) and we need a business card designed. We only see animal eyes - we are not a regular veterinary clinic. We already have a logo. We are looking for a professional, good looking business card to hand out to our clients. We are looking for something simple but professional and contemporary. Our logo is likely the only picture/graphic that needs to be on the card.
Updates

Contact Information for Business Card

Delia Vossman, BSc, DVM, MSc, DipACVO
Veterinary Ophthalmologist

Phone: 250.418.3927
Email: ridgelinepetvisioncare@mailbox-example.net
Website: ridgelinepetvisioncare-example.net
Address: 1874 Thornbury Rd
Kelowna, BC, V1X 4M9

Colors

Designer to choose colors to be used in the design.

Requirements
Must have
• Our logo (attached)

```html
<!DOCTYPE html>
<html lang="en">
<head>
<meta charset="utf-8">
<title>Ridgeline Pet Vision Care – Business Card</title>
<link href="https://fonts.googleapis.com/css2?family=Open+Sans:wght@400;600;700&display=swap" rel="stylesheet">
<style>
  :root {
    --backdrop: #3a3a3a;
    --card: #6a6a6a;
    --art-light: #747474;
    --art-dark: #555555;
    --teal: #0e9aa7;
    --white: #f4f4f4;
  }
  * { margin: 0; padding: 0; box-sizing: border-box; }
  html, body {
    width: 1200px; height: 1125px; overflow: hidden;
    background: var(--backdrop);
    font-family: "Open Sans", Arial, sans-serif;
  }
  .card {
    position: absolute; left: 150px;
    width: 900px; height: 514px;
    background: var(--card);
    border-bottom: 5px solid var(--teal);
    overflow: hidden;
  }
  .card--front { top: 30px; }
  .card--back { top: 581px; }

  .artwork {
    position: absolute; border-radius: 50%;
    background: radial-gradient(circle at 45% 40%, var(--art-light), var(--art-dark) 75%);
  }
  .card--front .artwork { left: 30px; top: 40px; width: 470px; height: 470px; }
  .card--back .artwork { left: 500px; top: 40px; width: 440px; height: 440px; }

  .wordmark {
    color: var(--teal); font-weight: 600;
    text-transform: uppercase; line-height: 1.15;
  }
  .wordmark__top, .wordmark__bottom { display: block; }
  .wordmark__top { letter-spacing: 0.55em; }
  .wordmark__bottom { letter-spacing: 0.04em; }

  .front-name {
    position: absolute; right: 50px; top: 215px;
    text-align: right; font-size: 32px;
  }
  .front-name .wordmark__top { margin-right: -0.55em; }

  .brand {
    position: absolute; left: 40px; top: 34px;
    display: flex; align-items: center; gap: 16px;
  }
  .brand__dot { width: 46px; height: 46px; border-radius: 50%; background: var(--teal); flex: none; }
  .brand .wordmark { font-size: 22px; }

  .contact { position: absolute; left: 40px; top: 130px; color: var(--white); z-index: 1; }
  .person { display: flex; align-items: center; gap: 12px; }
  .person__marker { width: 0; height: 0; border-top: 10px solid transparent; border-bottom: 10px solid transparent; border-left: 16px solid var(--teal); }
  .person__name {
    color: var(--teal); font-weight: 700; font-size: 26px; letter-spacing: 4px;
    text-transform: uppercase;
  }
  .person__credentials { color: var(--teal); font-size: 19px; margin: 4px 0 0 28px; }
  .person__title { font-size: 21px; margin: 2px 0 0 28px; }
  .address { font-size: 21px; line-height: 1.35; margin: 24px 0 0 12px; }
  .lines { list-style: none; margin: 16px 0 0 0; font-size: 19px; line-height: 1.55; }
  .lines li { display: flex; align-items: center; gap: 8px; }
  .lines svg { width: 18px; height: 18px; fill: var(--teal); flex: none; }
</style>
</head>
<body>
  <section class="card card--front">
    <div class="artwork" role="img" aria-label="Embossed tone-on-tone illustration of a horse, dog and cat"></div>
    <p class="wordmark front-name">
      <span class="wordmark__top">Ridgeline</span>
      <span class="wordmark__bottom">Pet Vision Care</span>
    </p>
  </section>

  <section class="card card--back">
    <div class="brand">
      <span class="brand__dot"></span>
      <p class="wordmark">
        <span class="wordmark__top">Ridgeline</span>
        <span class="wordmark__bottom">Pet Vision Care</span>
      </p>
    </div>

    <div class="contact">
      <div class="person">
        <span class="person__marker"></span>
        <span class="person__name">Delia Vossman</span>
      </div>
      <p class="person__credentials">BSc, DVM, MSc, DipACVO</p>
      <p class="person__title">Veterinary Ophthalmologist</p>

      <p class="address">1874 Thornbury Rd<br>Kelowna, BC, V1X 4M9</p>

      <ul class="lines">
        <li><svg viewBox="0 0 24 24"><path d="M6.6 10.8a15 15 0 0 0 6.6 6.6l2.2-2.2c.3-.3.7-.4 1-.2 1.1.4 2.3.6 3.6.6.6 0 1 .4 1 1V20c0 .6-.4 1-1 1A17 17 0 0 1 3 4c0-.6.4-1 1-1h3.5c.6 0 1 .4 1 1 0 1.3.2 2.5.6 3.6.1.3 0 .7-.2 1z"/></svg>250.418.3927</li>
        <li><svg viewBox="0 0 24 24"><path d="M2 5h20v14H2zm2 2v.4l8 5 8-5V7l-8 5z"/></svg>ridgelinepetvisioncare@mailbox-example.net</li>
        <li><svg viewBox="0 0 24 24"><path d="M12 2a10 10 0 1 0 0 20 10 10 0 0 0 0-20zm6.9 6h-3a15 15 0 0 0-1.3-3.9A8 8 0 0 1 18.9 8zM12 4c.8 1.2 1.5 2.5 1.9 4h-3.8c.4-1.5 1.1-2.8 1.9-4zM4.3 14a8 8 0 0 1 0-4h3.4a16 16 0 0 0 0 4zm.8 2h3a15 15 0 0 0 1.3 3.9A8 8 0 0 1 5.1 16zm3-8h-3a8 8 0 0 1 4.3-3.9C8.8 5.3 8.4 6.6 8.1 8zM12 20c-.8-1.2-1.500-2.5-1.9-4h3.8c-.4 1.5-1.1 2.8-1.9 4zm2.3-6H9.7a14 14 0 0 1 0-4h4.6a14 14 0 0 1 0 4zm.3 5.9c.6-1.2 1-2.5 1.3-3.9h3a8 8 0 0 1-4.3 3.9zm1.7-5.9a16 16 0 0 0 0-4h3.4a8 8 0 0 1 0 4z"/></svg>ridgelinepetvisioncare-example.net</li>
      </ul>
    </div>

    <div class="artwork" role="img" aria-label="Embossed tone-on-tone illustration of a horse, cat and dog"></div>
  </section>
</body>
</html>
```